New Property development signage

large poster for a new development.
3 metres x 2 metres. To include the following.

Tresswick Gardens
TO LET
LUXURY FULLY FURNISHED LARGE
2 AND 3 BED APARTMENTS
Garrold Estates
362 4150
www.garroldestates-example.com

Need this to be large simple writing with Garrold estates logo on the bottom

Target Market(s)

High end rental property market

Industry/Entity Type

Real Estate Development

Colors
000000
cbcbcb
0555a3

Requirements
Must have
• Name of the development must be in a different font, classic style
Nice to have
• Light Grey background, blues for colours
Should not have
• anymore than 3 /4 colours

```html
<!DOCTYPE html>
<html lang="en">
<head>
<meta charset="utf-8">
<title>To Let – Tresswick Gardens</title>
<link rel="stylesheet" href="https://fonts.googleapis.com/css2?family=Cinzel:wght@700&family=Jost:wght@400;600;700&display=swap">
<style>
  :root {
    --brand-navy: #283a8c;
    --sign-white: #ffffff;
  }
  html, body {
    margin: 0;
    padding: 0;
    width: 1200px;
    height: 800px;
    overflow: hidden;
    background: var(--sign-white);
  }
  .sign {
    display: block;
    width: 1200px;
    height: 800px;
    font-family: "Jost", "Century Gothic", sans-serif;
  }
  .header-band { fill: var(--brand-navy); }
  .headline { fill: var(--sign-white); font-size: 178px; }
  .headline-strong { font-weight: 700; }
  .headline-light { font-weight: 400; }
  .detail-line { fill: var(--brand-navy); font-weight: 600; }
  .development-name {
    fill: var(--brand-navy);
    font-family: "Cinzel", "Times New Roman", serif;
    font-weight: 700;
  }
  .rule { stroke: var(--brand-navy); stroke-width: 3; }
  .agent-name { fill: var(--brand-navy); font-weight: 600; font-size: 64px; }
  .agent-mark { fill: var(--brand-navy); }
  .web-address { fill: var(--brand-navy); font-weight: 600; font-size: 42px; }
</style>
</head>
<body>
<svg class="sign" viewBox="0 0 1200 800" xmlns="http://www.w3.org/2000/svg" role="img" aria-label="To let sign for Tresswick Gardens">
  <rect class="header-band" x="0" y="0" width="1200" height="195"/>
  <text class="headline" x="600" y="172" text-anchor="middle"><tspan class="headline-strong">TO</tspan><tspan class="headline-light">LET</tspan></text>

  <text class="detail-line" x="95" y="284" font-size="82" textLength="1010" lengthAdjust="spacingAndGlyphs">LUXURY FULLY FURNISHED</text>
  <line class="rule" x1="95" y1="298" x2="1103" y2="298"/>

  <text class="detail-line" x="95" y="367" font-size="64" textLength="1010" lengthAdjust="spacingAndGlyphs">LARGE 2 AND 3 BED APARTMENTS</text>
  <line class="rule" x1="95" y1="378" x2="1103" y2="378"/>

  <text class="development-name" x="95" y="460" font-size="86" textLength="1010" lengthAdjust="spacingAndGlyphs">TRESSWICK GARDENS</text>

  <line class="rule" x1="95" y1="506" x2="398" y2="506"/>
  <text class="detail-line" x="600" y="540" font-size="80" text-anchor="middle" textLength="380" lengthAdjust="spacingAndGlyphs">362 4150</text>
  <line class="rule" x1="800" y1="506" x2="1103" y2="506"/>

  <rect class="agent-mark" x="378" y="618" width="34" height="34"/>
  <text class="agent-name" x="430" y="658">Garrold Estates</text>

  <text class="web-address" x="600" y="778" text-anchor="middle" textLength="640" lengthAdjust="spacingAndGlyphs">www.garroldestates-example.com</text>
</svg>
</body>
</html>
```